Letterhead for a German Distribution/Manufacturing Company

We need a professional Letterhead in a unique Design.
not to playful.
The Letterhead has to show show that we are a international company with headquater in Germany.
all details like adress, Vat Tax Number, Bank Accout, Eori, email, Company number has to be on the Letterhead.
for example use: VAT TAX DE5470318 Bank Account: Kestrel Bank IBAN DE412058731ß204683 Swift: MORV0417352 EORI 3150428697 Company Number: HRB 51806 Adress: VOLMINTA UG Ahornweg 7 Postal Code 06384 City Hallwenstadt Country: Germany Email: info@volminta-example.com
the design can be colored but doesnt have to be
Industry/Entity Type
Manufacturing and international distribution
Requirements
Must have
- show that we are a international company with headquater in Germany. our company infos and logo

```html
<!DOCTYPE html>
<html lang="en">
<head>
<meta charset="utf-8">
<title>VOLMINTA UG Letterhead</title>
<link rel="stylesheet" href="https://fonts.googleapis.com/css2?family=Open+Sans:wght@400&family=Roboto:ital,wght@0,400;1,400&display=swap">
<style>
  :root {
    --backdrop: #6f716f;
    --paper: #ffffff;
    --ink: #3a3a3a;
    --ink-soft: #4a4a4a;
    --brand: #2e2e2e;
    --signature-tone: #e6e8ee;
  }
  * { box-sizing: border-box; margin: 0; padding: 0; }
  html, body {
    width: 1200px; height: 938px; overflow: hidden;
    background: var(--backdrop);
  }
  .letterhead {
    position: absolute; left: 282px; top: 19px;
    width: 636px; height: 900px;
    background: var(--paper);
    box-shadow: 0 6px 24px rgba(0,0,0,.35);
    color: var(--ink);
  }
  .brand {
    position: absolute; left: 52px; top: 52px;
    display: flex; align-items: center; gap: 8px;
    font-family: "Roboto", sans-serif; font-weight: 400;
    font-size: 25px; letter-spacing: .5px; color: var(--brand);
  }
  .brand-dot { width: 22px; height: 22px; border-radius: 50%; background: var(--brand); }
  .company-address {
    position: absolute; left: 330px; top: 52px;
    font-family: "Roboto", sans-serif; font-style: italic;
    font-size: 9.5px; line-height: 13px; color: var(--ink-soft);
  }
  .company-contact {
    position: absolute; left: 462px; top: 48px;
    list-style: none;
    font-family: "Roboto", sans-serif; font-style: italic;
    font-size: 9.5px; line-height: 13px; color: var(--ink-soft);
  }
  .company-contact li { display: flex; align-items: center; gap: 5px; white-space: nowrap; }
  .company-contact svg { width: 8px; height: 8px; fill: var(--ink-soft); flex: none; }
  .letter-body {
    position: absolute; left: 70px; top: 196px; width: 500px;
    font-family: "Open Sans", sans-serif; font-size: 10.5px;
    line-height: 15px; color: var(--ink);
  }
  .letter-body p { margin-bottom: 13px; }
  .letter-body .salutation { margin-bottom: 10px; }
  .signature {
    width: 70px; height: 52px; margin-top: 6px;
    background: var(--signature-tone); border-radius: 4px;
  }
  .legal-footer {
    position: absolute; left: 0; right: 0; bottom: 34px;
    text-align: center;
    font-family: "Roboto", sans-serif; font-style: italic;
    font-size: 9.5px; line-height: 14px; color: var(--ink-soft);
  }
</style>
</head>
<body>
  <article class="letterhead">
    <header>
      <div class="brand"><span class="brand-dot"></span><span>VOLMINTA</span></div>
      <address class="company-address">
        VOLMINTA UG<br>Ahornweg 7 06384<br>City Hallwenstadt Germany
      </address>
      <ul class="company-contact">
        <li><svg viewBox="0 0 10 10"><path d="M2 1 L4 1 L5 3.5 L3.8 4.5 Q5 6.5 5.5 6.2 L6.5 5 L9 6 L9 8 Q8.5 9 7 9 Q1 7 1 2 Q1 1 2 1Z"/></svg>555.014.2860</li>
        <li><svg viewBox="0 0 10 10"><path d="M0 2 H10 V8 H0Z M0 2 L5 5.5 L10 2" stroke="#fff" stroke-width=".8"/></svg>info@volminta-example.com</li>
        <li><svg viewBox="0 0 10 10"><circle cx="5" cy="5" r="4.5"/></svg>www.volminta-example.com</li>
      </ul>
    </header>

    <section class="letter-body">
      <p class="salutation">Dear customer,</p>
      <p>Lorem ipsum dolor sit amet, consectetur adipisicing elit, sed do eiusmod tempor incididunt ut labore et dolore magna aliqua. Ut enim ad minim veniam, quis nostrud exercitation ullamco laboris nisi ut aliquip ex ea commodo consequat. Duis aute irure dolor in reprehenderit in voluptate velit esse cillum dolore eu fugiat nulla pariatur. Excepteur sint occaecat cupidatat non proident, sunt in culpa qui officia deserunt mollit anim id est laborum.</p>
      <p>Lorem ipsum dolor sit amet, consectetur adipisicing elit, sed do eiusmod tempor incididunt ut labore et dolore magna aliqua. Ut enim ad minim veniam, quis nostrud exercitation ullamco laboris nisi ut aliquip ex ea commodo consequat. Duis aute irure dolor in reprehenderit in voluptate velit esse cillum dolore eu fugiat nulla pariatur. Excepteur sint occaecat cupidatat non proident, sunt in culpa qui officia deserunt mollit anim id est laborum.</p>
      <p>Lorem ipsum dolor sit amet, consectetur adipisicing elit, sed do eiusmod tempor incididunt ut labore et dolore magna aliqua. Ut enim ad minim veniam, quis nostrud exercitation ullamco laboris nisi ut aliquip ex ea commodo consequat. Duis aute irure dolor in reprehenderit in voluptate velit esse cillum dolore eu fugiat nulla pariatur. Excepteur sint occaecat cupidatat non proident, sunt in culpa qui officia deserunt mollit anim id est laborum.</p>
      <p>Lorem ipsum dolor sit amet, consectetur adipisicing elit, sed do eiusmod tempor incididunt ut labore et dolore magna aliqua. Ut enim ad minim veniam, quis nostrud exercitation ullamco laboris nisi ut aliquip ex ea commodo consequat. Duis aute irure dolor in reprehenderit.</p>
      <p>Yours Sincerely,</p>
      <div class="signature" role="img" aria-label="Handwritten signature"></div>
    </section>

    <footer class="legal-footer">
      VAT TAX DE5470318 | Bank Account: Kestrel Bank IBAN DE412058731ß204683<br>
      Swift: MORV0417352 EORI 3150428697 | Company Number: HRB 51806
    </footer>
  </article>
</body>
</html>
```